Cat-products company needs smart, yet endearing, business card

We need a business card design for a new, but up-and-running, business based in Honolulu, Hawaii. The business is Purrnest Nook Co. Our first product is the most environmentally-friendly cat grass kit ever seen on the planet. Future products, currently in the R&D phase, will include a variety of exciting cat scratchers. We also do consulting work to help apartment-dwellers make their home more cat-friendly and, in the future, plan on doing full, custom installs of structure to create high walkways for cats.

Target Market(s)

Middle-aged, apartment-dwelling, middle-class workers who own 1 or more cats and who dote on them.

Industry/Entity Type

Pet Care

Contact Information for Business Card

A striking, professional, yet warm and friendly design is what we're after.

Font styles to use
Serif
Sans Serif
Other font styles liked:
• Comfortaa

Colors

Designer to choose colors to be used in the design.

Requirements
Must have
• The company logo: (see attachment)
• The company name: Purrnest Nook Co
• The web address: www.purrnestnookco.com
• Email: support@purrnestnookco.com
• Phone: +1 (808) 571 6023
• Update (Fri Jun 30 3017 7:45pm Hawaii Time) I would like, is possible, uploaded picture of the cat grass kit on the back of the card with some text along the lines of: Purrnest Nook Co - Maker Of The Leafiest Feline Sprout Set Yet
Nice to have
• A cat picture, cartoon, real or silhouette that illustrates cats in action and/or relaxing; ie using the apartment space to live, play and relax in and being well-contented.
• Most of the website is done in the font: Comfortaa. It might be nice to continue using this for brand consistency.
Should not have
• Hard-to-read fonts.

```html
<!DOCTYPE html>
<html lang="en">
<head>
<meta charset="utf-8">
<title>Purrnest Nook Co – Business Card</title>
<link href="https://fonts.googleapis.com/css2?family=Comfortaa:wght@400;700&display=swap" rel="stylesheet">
<style>
  :root {
    --stage: #1f1f1f;
    --card-brown: #553430;
    --accent-yellow: #f6ab1c;
    --text-light: #ffffff;
    --text-soft: #f3e9e4;
    --photo-light: #eeeae3;
    --photo-sisal: #d9c7a4;
    --photo-ginger: #c98a4a;
  }
  * { box-sizing: border-box; margin: 0; padding: 0; }
  html, body {
    width: 1200px;
    height: 1076px;
    overflow: hidden;
  }
  body {
    background: var(--stage);
    font-family: "Comfortaa", sans-serif;
    position: relative;
  }
  .card {
    position: absolute;
    left: 180px;
    width: 840px;
    height: 480px;
    background: var(--card-brown);
    overflow: hidden;
  }
  .card--front { top: 38px; }
  .card--back  { top: 558px; }

  /* Front */
  .front-brand {
    position: absolute;
    inset: 0;
    display: flex;
    flex-direction: column;
    align-items: center;
    justify-content: center;
    gap: 22px;
  }
  .brand-mark {
    width: 84px;
    height: 84px;
    background: var(--accent-yellow);
  }
  .brand-name {
    font-weight: 700;
    font-size: 58px;
    color: var(--text-light);
    letter-spacing: 1px;
  }
  .front-url {
    font-weight: 700;
    font-size: 22px;
    color: var(--text-light);
    letter-spacing: 0.5px;
    margin-top: 6px;
  }

  /* Back */
  .back-photo {
    position: absolute;
    left: 0;
    top: 0;
    width: 380px;
    height: 100%;
    background: linear-gradient(120deg, var(--photo-light) 0%, var(--photo-light) 35%, var(--photo-sisal) 60%, var(--photo-ginger) 100%);
  }
  .back-details {
    position: absolute;
    left: 425px;
    top: 70px;
    right: 30px;
    bottom: 60px;
  }
  .employee-name {
    font-weight: 700;
    font-size: 34px;
    color: var(--accent-yellow);
    line-height: 1;
  }
  .employee-role {
    font-weight: 400;
    font-size: 22px;
    color: var(--text-soft);
    margin-top: 2px;
  }
  .contact-list {
    list-style: none;
    position: absolute;
    left: 0;
    bottom: 0;
    display: flex;
    flex-direction: column;
    gap: 10px;
  }
  .contact-item {
    display: flex;
    align-items: center;
    gap: 12px;
    font-size: 21px;
    font-weight: 400;
    color: var(--text-light);
  }
  .contact-icon {
    width: 30px;
    height: 30px;
    background: var(--accent-yellow);
    flex: none;
    display: flex;
    align-items: center;
    justify-content: center;
  }
  .contact-icon svg { width: 22px; height: 22px; }
</style>
</head>
<body>

  <section class="card card--front" aria-label="Business card front">
    <div class="front-brand">
      <div class="brand-mark" aria-hidden="true"></div>
      <h1 class="brand-name">Purrnest Nook Co</h1>
      <p class="front-url">www.purrnestnookco.com</p>
    </div>
  </section>

  <section class="card card--back" aria-label="Business card back">
    <div class="back-photo" role="img" aria-label="Photo of cats climbing and resting on a tall sisal scratching post with wall shelves"></div>

    <div class="back-details">
      <h2 class="employee-name">EMPLOYEE NAME</h2>
      <p class="employee-role">Manager</p>

      <ul class="contact-list">
        <li class="contact-item">
          <span class="contact-icon" aria-hidden="true">
            <svg viewBox="0 0 24 24"><path fill="#553430" d="M6.6 10.8a15 15 0 0 0 6.6 6.6l2.2-2.2a1 1 0 0 1 1-.25 11.4 11.4 0 0 0 3.6.57 1 1 0 0 1 1 1V20a1 1 0 0 1-1 1A17 17 0 0 1 3 4a1 1 0 0 1 1-1h3.5a1 1 0 0 1 1 1c0 1.25.2 2.45.57 3.57a1 1 0 0 1-.25 1z"/></svg>
          </span>
          +1 (808) 571 6023
        </li>
        <li class="contact-item">
          <span class="contact-icon" aria-hidden="true">
            <svg viewBox="0 0 24 24"><rect x="3" y="6" width="18" height="12" fill="none" stroke="#553430" stroke-width="2"/><path d="M3 6l9 7 9-7" fill="none" stroke="#553430" stroke-width="2"/></svg>
          </span>
          support@purrnestnookco.com
        </li>
        <li class="contact-item">
          <span class="contact-icon" aria-hidden="true">
            <svg viewBox="0 0 24 24" fill="none" stroke="#553430" stroke-width="1.8"><circle cx="12" cy="12" r="9"/><ellipse cx="12" cy="12" rx="4" ry="9"/><path d="M3 12h18M5 7.5h14M5 16.5h14"/></svg>
          </span>
          www.purrnestnookco.com
        </li>
      </ul>
    </div>
  </section>

</body>
</html>
```